Bespoke Builders Business Card Design

We need a business card for an established builder of high quality bespoke homes in Auckland and Northland. We build and renovate homes collaboratively facilitating effective communication between owners, builders, architects, suppliers and tradespeople. We have never built or renovated a home that leaks or has faults. We only use reliable materials. We have never been sued or had legal action taken against us. We are honest builders of bespoke homes not group mass produced homes. Our niche market is in character homes. We practice sustainability and have built a lot of coastal property. We have been in business for over thirty years . We would like to see natural colors of the environment sand,sea and maybe vegetation . The design should communicate quality, sustainability,fair pricing, open communication and the originality of bespoke building. And the fact that the builder is registered.

Industry/Entity Type

Business

Contact Information for Business Card

Rowan Tellick Builders
Ph. 021583917
18 Kestrel Rd Harwood Bay Auckland 0814
PO Box 927 Mangawhai 0583

```html
<!DOCTYPE html>
<html lang="en">
<head>
<meta charset="utf-8">
<title>Rowan Tellick Builders – Business Card</title>
<link rel="stylesheet" href="https://fonts.googleapis.com/css2?family=Tinos:wght@400;700&display=swap">
<style>
  :root {
    --page-bg: #ebe6dc;
    --sea-deep: #123a3b;
    --sea-glow: #1f5755;
    --forest-deep: #1d3121;
    --forest-glow: #2f4a31;
    --sand: #e6d8bb;
    --sand-light: #f6efe0;
    --vegetation: #5f7c3f;
  }
  * { margin: 0; padding: 0; box-sizing: border-box; }
  html, body {
    width: 1200px;
    height: 892px;
    overflow: hidden;
    background: var(--page-bg);
    font-family: "Tinos", "Times New Roman", serif;
  }
  .sheet {
    width: 1200px;
    height: 892px;
    display: flex;
    flex-direction: column;
    align-items: center;
    justify-content: center;
    gap: 60px;
  }
  .card {
    position: relative;
    width: 630px;
    height: 360px;
    overflow: hidden;
    box-shadow: 0 6px 18px rgba(0,0,0,0.22);
  }
  .card--front {
    background: radial-gradient(ellipse at 62% 35%, var(--sea-glow), var(--sea-deep) 72%);
  }
  .card--back {
    background: radial-gradient(ellipse at 45% 40%, var(--forest-glow), var(--forest-deep) 72%);
    display: flex;
    align-items: center;
    justify-content: center;
  }
  .swoosh {
    position: absolute;
    inset: 0;
    width: 100%;
    height: 100%;
  }
  .swoosh__fill { fill: var(--sand); }
  .swoosh__stripe { fill: var(--vegetation); }
  .front-content {
    position: absolute;
    top: 46px;
    right: 36px;
    width: 360px;
    color: var(--sand-light);
    text-align: center;
  }
  .business-name {
    font-weight: 700;
    font-size: 33px;
    line-height: 1;
    text-align: right;
    letter-spacing: 0.3px;
    white-space: nowrap;
  }
  .name-rule {
    height: 2px;
    background: var(--sand);
    margin: 14px 0 0 16px;
  }
  .contact {
    margin-top: 38px;
    padding-left: 30px;
    font-size: 17px;
    line-height: 1.7;
    font-style: normal;
    white-space: nowrap;
  }
  .back-name {
    color: var(--sand-light);
    font-weight: 700;
    font-size: 46px;
    letter-spacing: 0.8px;
    white-space: nowrap;
  }
</style>
</head>
<body>
<main class="sheet">
  <section class="card card--front" aria-label="Business card front">
    <svg class="swoosh" viewBox="0 0 630 360" preserveAspectRatio="none" aria-hidden="true">
      <path class="swoosh__fill" d="M0 40 C 140 70, 262 200, 300 360 L0 360 Z"/>
      <path class="swoosh__stripe" d="M18 60 C 150 98, 250 220, 272 360 L 256 360 C 232 232, 142 114, 18 60 Z"/>
    </svg>
    <div class="front-content">
      <h1 class="business-name">Rowan Tellick Builders</h1>
      <div class="name-rule"></div>
      <address class="contact">
        <div class="contact__phone">021583917</div>
        <div class="contact__street">18 Kestrel Rd Harwood Bay</div>
        <div class="contact__postal">Auckland 0814 PO Box 927 Mangawhai 0583</div>
      </address>
    </div>
  </section>

  <section class="card card--back" aria-label="Business card back">
    <h2 class="back-name">Rowan Tellick Builders</h2>
  </section>
</main>
</body>
</html>
```